New business card/stationary for a consulting company

I am looking for a clean and very professional looking business card for my consulting company as well as corresponding stationary. I am uploading our logo. I like simple and powerful for the feel. No graphics but I am open on everything else. Below is my contact information but would like the final to be in a version I can add my employees information into and print. Thank you.

Daniel Whitcombe
dan@ferncliffadvisory.com
2870 North 9th Avenue, Summit Floor, Elm Ridge, Illinois 60531
www.ferncliffadvisory.com

Industry/Entity Type

Consulting

Contact Information for Business Card

Daniel Whitcombe
dan@ferncliffadvisory.com
www.ferncliffadvisory.com

Font styles to use
Serif
Sans Serif

Requirements
Must have
• Our logo and the business card details.
Nice to have
• our website www.ferncliffadvisory.com

```html
<!DOCTYPE html>
<html lang="en">
<head>
<meta charset="utf-8">
<title>Ferncliff Advisory – Business Card</title>
<link href="https://fonts.googleapis.com/css2?family=Montserrat:wght@300;400;500;700&display=swap" rel="stylesheet">
<style>
  :root{
    --brand-blue:#0b0ca8;
    --paper:#ffffff;
    --backdrop:#eceef0;
    --rule:#ffffff;
  }
  *{box-sizing:border-box;margin:0;padding:0}
  html,body{width:1200px;height:900px;overflow:hidden;background:var(--backdrop)}
  body{font-family:'Montserrat',sans-serif;position:relative}

  .card{position:absolute;left:280px;width:640px;height:366px;overflow:hidden;
        box-shadow:0 2px 10px rgba(0,0,0,.12)}
  .card--front{top:50px;background:var(--brand-blue);color:var(--paper)}
  .card--back{top:470px;background:var(--paper)}

  /* front */
  .front-brand{position:absolute;left:0;right:0;top:120px;display:flex;align-items:center;justify-content:center;gap:18px}
  .brand-square{width:26px;height:26px;background:var(--paper)}
  .front-brand .brand-name{font-size:38px;font-weight:300;letter-spacing:2px;color:var(--paper)}
  .front-rule{position:absolute;left:60px;right:60px;top:270px;display:flex;align-items:center;gap:14px}
  .front-rule .line{flex:1;height:2px;background:var(--rule)}
  .front-rule .url{font-size:12px;font-weight:700;letter-spacing:.3px}

  /* back */
  .back-brand{position:absolute;left:0;right:0;top:48px;display:flex;align-items:center;justify-content:center;gap:14px}
  .back-brand .brand-square{background:var(--brand-blue);width:22px;height:22px}
  .back-brand .brand-name{font-size:28px;font-weight:400;letter-spacing:1.5px;color:var(--brand-blue)}
  .back-band{position:absolute;left:0;top:158px;width:640px;height:208px}
  .details{position:absolute;left:0;top:158px;width:640px;height:208px;color:var(--paper)}
  .person{position:absolute;left:60px;top:40px}
  .person-name{font-size:22px;font-weight:700;margin-bottom:6px}
  .person-title{font-size:14px;font-weight:700;margin-bottom:10px}
  .person-address{font-size:13px;font-weight:400;line-height:1.9}
  .divider{position:absolute;left:372px;top:36px;width:2px;height:120px;background:var(--rule)}
  .contact-list{position:absolute;left:398px;top:38px;list-style:none}
  .contact-list li{display:flex;align-items:center;gap:10px;font-size:13px;font-weight:400;height:28px}
  .contact-list svg{width:13px;height:13px;flex:none}
</style>
</head>
<body>

<section class="card card--front" aria-label="Business card front">
  <div class="front-brand">
    <span class="brand-square"></span>
    <span class="brand-name">FERNCLIFF ADVISORY</span>
  </div>
  <div class="front-rule">
    <span class="line"></span>
    <span class="url">www.ferncliffadvisory.com</span>
    <span class="line"></span>
  </div>
</section>

<section class="card card--back" aria-label="Business card back">
  <div class="back-brand">
    <span class="brand-square"></span>
    <span class="brand-name">FERNCLIFF ADVISORY</span>
  </div>
  <svg class="back-band" viewBox="0 0 640 208" aria-hidden="true">
    <polygon points="0,0 76,0 84,10 92,0 640,0 640,208 0,208" fill="var(--brand-blue)"/>
  </svg>
  <div class="details">
    <div class="person">
      <p class="person-name">Daniel Whitcombe</p>
      <p class="person-title">Founder / Principal</p>
      <p class="person-address">2870 North 9th Avenue, Summit Floor,<br>Elm Ridge, Illinois 60531</p>
    </div>
    <span class="divider"></span>
    <ul class="contact-list">
      <li><svg viewBox="0 0 16 16"><path fill="#fff" d="M3 1l3 3-1.5 2a9 9 0 0 0 5.5 5.5L12 10l3 3-2 2C7 15 1 9 1 3z"/></svg>(855) 302 47716</li>
      <li><svg viewBox="0 0 16 16"><rect x="4" y="1" width="8" height="14" rx="1.5" fill="none" stroke="#fff" stroke-width="1.6"/><circle cx="8" cy="12.5" r="1" fill="#fff"/></svg>+917304218556</li>
      <li><svg viewBox="0 0 16 16"><rect x="1" y="3" width="14" height="10" fill="#fff"/><path d="M1 3l7 6 7-6" fill="none" stroke="var(--brand-blue)" stroke-width="1.4"/></svg>dan@ferncliffadvisory.com</li>
      <li><svg viewBox="0 0 16 16"><circle cx="8" cy="8" r="7" fill="#fff"/><path d="M1 8h14M8 1c-3 4-3 10 0 14M8 1c3 4 3 10 0 14" fill="none" stroke="var(--brand-blue)" stroke-width="1"/></svg>www.ferncliffadvisory.com</li>
    </ul>
  </div>
</section>

</body>
</html>
```